World Class Presentation folder for a National Designer of innovative building products

We are a National Designer, Manufacturer, and distributor of aluminum and stainless Balconies, Railings, Sunshades, and Patio Covers. We sell our products and services to the very best commercial condo and residential builders in the country. This Brochure folder will be the first piece of literature that we give to our customers, and want to WOW them at first glance with a world-class design and look.

We already have a logo and website but would like you to visit https://harborlineframeworks.example and view the projects and product information to help inspire you to create an award-winning piece of literature for us.

Besides putting literature in it, the folder must have a place to hold a business card.

Thank you in advance for your great designs, and I look forward to working with you.
Dean Holtzmarrick
President | Pacific, WA
417.629.5810 ext 305

```html
<!DOCTYPE html>
<html lang="en">
<head>
<meta charset="utf-8">
<title>Harborline Frameworks — Presentation Folder</title>
<link href="https://fonts.googleapis.com/css2?family=Michroma&family=Roboto:wght@400&display=swap" rel="stylesheet">
<style>
  :root {
    --page-bg: #d6d6d8;
    --brand-red: #c81c48;
    --brand-red-dark: #9c1434;
    --ink: #1f1f24;
    --white: #ffffff;
    --band-white: #f4f4f5;
    --photo-sky: #e9ecef;
    --photo-facade: #cfd4d8;
    --photo-patio: #cdd2c6;
    --photo-brick: #c8bdb4;
  }
  * { box-sizing: border-box; margin: 0; padding: 0; }
  html, body { width: 1200px; height: 847px; overflow: hidden; }
  body {
    background: var(--page-bg);
    display: flex;
    align-items: center;
    justify-content: center;
    font-family: "Roboto", Arial, sans-serif;
  }
  .folder-spread {
    display: flex;
    width: 880px;
    height: 620px;
    box-shadow: 0 18px 40px rgba(0,0,0,0.22);
  }
  .panel { width: 440px; height: 620px; position: relative; overflow: hidden; }

  /* Back cover */
  .back-cover {
    background: linear-gradient(90deg, var(--brand-red-dark) 0%, var(--brand-red) 45%, var(--brand-red) 70%, var(--brand-red-dark) 100%);
    color: var(--white);
  }
  .back-cover .wordmark {
    position: absolute;
    top: 200px; left: 0; right: 0;
    text-align: center;
  }
  .wordmark-name {
    font-family: "Michroma", "Arial Black", sans-serif;
    font-size: 30px;
    letter-spacing: 2px;
    line-height: 1.25;
  }
  .wordmark-dot {
    display: inline-block;
    width: 14px; height: 14px;
    margin-bottom: 14px;
  }
  .back-cover .wordmark-dot { background: var(--white); }
  .contact-block {
    position: absolute;
    bottom: 70px; left: 0; right: 0;
    text-align: center;
    font-size: 12px;
    line-height: 1.45;
    letter-spacing: 0.3px;
  }

  /* Front cover */
  .front-cover { background: var(--band-white); }
  .photo {
    position: absolute; left: 0; right: 0;
    display: flex;
  }
  .photo-top { top: 0; height: 220px; }
  .photo-bottom { bottom: 0; height: 240px; }
  .photo-tile { flex: 1; height: 100%; opacity: 0.75; }
  .tile-facade { background: linear-gradient(160deg, var(--photo-sky), var(--photo-facade)); }
  .tile-railing { background: linear-gradient(200deg, var(--photo-sky), #bcc5c9); }
  .tile-patio { background: linear-gradient(180deg, #dfe2dc, var(--photo-patio)); }
  .tile-entry { background: linear-gradient(180deg, #e2dcd6, var(--photo-brick)); }
  .logo-band {
    position: absolute;
    top: 226px; left: 0; right: 0;
    height: 148px;
    background: var(--band-white);
    border-top: 4px solid var(--brand-red);
    border-bottom: 4px solid var(--brand-red);
    display: flex;
    align-items: center;
    justify-content: center;
  }
  .front-cover .wordmark { text-align: center; color: var(--ink); }
  .front-cover .wordmark-dot { background: var(--brand-red); }
</style>
</head>
<body>
  <main class="folder-spread">
    <section class="panel back-cover" aria-label="Back cover">
      <div class="wordmark">
        <span class="wordmark-dot"></span>
        <p class="wordmark-name">HARBORLINE<br>FRAMEWORKS</p>
      </div>
      <address class="contact-block" style="font-style:normal">
        Harborline Frameworks<br>
        1450 Cedar Mill Rd NE<br>
        Auburn Ridge, WA 98311<br>
        P : 417-629-5810&nbsp; P : 866-412-3075<br>
        F : 417-629-5842
      </address>
    </section>

    <section class="panel front-cover" aria-label="Front cover">
      <div class="photo photo-top">
        <div class="photo-tile tile-facade" role="img" aria-label="Photo of an apartment facade with aluminum balconies and sunshades"></div>
        <div class="photo-tile tile-railing" role="img" aria-label="Photo of a glass and aluminum balcony railing overlooking city towers"></div>
      </div>
      <div class="logo-band">
        <div class="wordmark">
          <span class="wordmark-dot"></span>
          <p class="wordmark-name">HARBORLINE<br>FRAMEWORKS</p>
        </div>
      </div>
      <div class="photo photo-bottom">
        <div class="photo-tile tile-patio" role="img" aria-label="Photo of a covered patio with outdoor seating beside a pool"></div>
        <div class="photo-tile tile-entry" role="img" aria-label="Photo of a building entry with a metal railing and brick wall"></div>
      </div>
    </section>
  </main>
</body>
</html>
```